Stationary Set Rebrand for Brennick

We are a Canadian Distribution and Service Company that was established in 1969. Over the past 5 decades we have expanded our business and have warehouses across Canada. We specialize in adhesive tapes, adhesives, films, safety, warehouse, shipping, janitorial and packaging supplies.

We have updated our logo design and would like a new corporate branding identity that includes a new fresh Stationary Set (Business Cards, Letterhead, Letterhead MS Word, Envelope, Presentation Folders, Email Signatures, Notepad Covers, etc.)

Target Market(s)

Industrial Business Sector

Font styles to use
Sans Serif

Colors
0054AA
0677BA
7BADD7
CADEEF
E8F1F8
0094D4
00A9DD
6FCCEA
C7EBF8
E9F6FB
00AB8E
00BBA5
67D7C9
C6EFE9
E9F9F6
EB3D1F
EC4F4E
F09395
F8D3D4
FCEDEE

Requirements
Should not have
• Colors not too light, darker colours preferred

```html
<!DOCTYPE html>
<html lang="en">
<head>
<meta charset="utf-8">
<title>Brennick Business Card</title>
<link href="https://fonts.googleapis.com/css2?family=Nunito+Sans:wght@400;600;800&display=swap" rel="stylesheet">
<style>
  :root {
    --backdrop: #9b9b9b;
    --card: #161616;
    --card-emboss: #2c2c2c;
    --edge: #c8141b;
    --accent: #e0252f;
    --text: #f2f2f2;
  }
  * { margin: 0; padding: 0; box-sizing: border-box; }
  html, body { width: 1200px; height: 1083px; overflow: hidden; }
  body {
    background: var(--backdrop);
    font-family: "Nunito Sans", Arial, sans-serif;
    color: var(--text);
    position: relative;
  }
  .card {
    position: absolute;
    left: 220px;
    width: 760px;
    height: 434px;
    background: var(--card);
    border-bottom: 5px solid var(--edge);
    border-right: 3px solid var(--edge);
    box-shadow: 0 18px 40px rgba(0,0,0,0.35);
  }
  .card-front { top: 70px; }
  .card-back { top: 580px; }

  .brand {
    position: absolute;
    display: flex;
    align-items: center;
    gap: 12px;
    font-weight: 800;
    line-height: 1;
  }
  .brand-mark { width: 14px; height: 14px; background: var(--accent); }
  .card-front .brand { left: 52px; top: 54px; font-size: 62px; color: var(--text); }

  .holder {
    position: absolute;
    right: 52px;
    top: 150px;
    padding-left: 16px;
    border-left: 2px solid var(--accent);
  }
  .holder-name {
    font-size: 26px;
    font-weight: 600;
    color: var(--accent);
    letter-spacing: 0.5px;
    text-transform: uppercase;
  }
  .holder-role { font-size: 17px; margin-top: 4px; }

  .contact {
    position: absolute;
    left: 52px;
    bottom: 48px;
    font-size: 17px;
    line-height: 1.45;
  }
  .contact-address { margin-bottom: 10px; }
  .contact-line { display: flex; align-items: center; gap: 12px; }
  .contact-line svg { width: 15px; height: 15px; flex: none; }

  .card-back .brand {
    left: 0; right: 0; top: 140px;
    justify-content: center;
    font-size: 80px;
    color: var(--card-emboss);
  }
  .founded {
    position: absolute;
    left: 0; right: 0; bottom: 70px;
    text-align: center;
    font-size: 18px;
  }
</style>
</head>
<body>
  <section class="card card-front">
    <div class="brand"><span class="brand-name">Brennick</span><span class="brand-mark"></span></div>

    <div class="holder">
      <div class="holder-name">Daniel Mercer</div>
      <div class="holder-role">Development Manager Officer</div>
    </div>

    <div class="contact">
      <div class="contact-address">412 Harbour Line<br>Suite 508, Halton, ON 41207</div>
      <div class="contact-line">
        <svg viewBox="0 0 16 16" aria-hidden="true"><path fill="#e0252f" d="M3.5 1.5l2.3 2.6-1.2 1.7c.9 2 2.4 3.6 4.4 4.6l1.7-1.2 2.6 2.3-1.4 2.3C6.6 13.5 2.5 9.4 1.2 3.1z"/></svg>
        <span>614-302-7781</span>
      </div>
      <div class="contact-line">
        <svg viewBox="0 0 16 16" aria-hidden="true"><rect x="1" y="3" width="14" height="10" fill="#e0252f"/><path d="M1 3l7 6 7-6" fill="none" stroke="#161616" stroke-width="1.3"/></svg>
        <span>daniel.mercer@brennickdirect.com</span>
      </div>
      <div class="contact-line">
        <svg viewBox="0 0 16 16" aria-hidden="true"><g fill="none" stroke="#e0252f" stroke-width="1.2"><circle cx="8" cy="8" r="6.5"/><ellipse cx="8" cy="8" rx="3" ry="6.5"/><path d="M1.5 8h13M2.5 4.8h11M2.5 11.2h11"/></g></svg>
        <span>brennickdirect.com</span>
      </div>
    </div>
  </section>

  <section class="card card-back">
    <div class="brand"><span class="brand-name">Brennick</span><span class="brand-mark"></span></div>
    <div class="founded">Estd. 1969</div>
  </section>
</body>
</html>
```